Granite Tile Retail Website

We need wireframe PSD for a website selling granite tile. There are 4 custom pages, shopping cart page, and checkout page. I have a logo designed but the color scheme is up to you.
Color Gallery - We have approximately 20 different stone colors. Each color will have a little gallery of its own pictures. On this page the customer can also add a sample piece of the color they are viewing to their shopping cart.
Questions Page - This page has 3 elements
1. Upload or fax diagram of kitchen for quotation
2. Installation video
3. Installation FAQ (text)
Order Page - This page has 3 steps for the customer
1. Customer chooses his color.
2. For each color we have numerous different products. He inputs the quantity of each product.
3. Customer is given total price and shipping quote. If order over $500 it says "This order qualifies for free shipping". Customer can click on button to "Order Now"
Shopping Cart - Very standard, just like I have attached here. Just modify for your colors / font.
Checkout - Just like in the attached. See design-explanation.docx for minor adjustments.
I have vector file for logo.
Updates
Please try to post your designs by tonightÂ
Target Market(s)
Home owners 40-60 years old
Industry/Entity Type
Shopping
Look and feel

```html
<!DOCTYPE html>
<html lang="en">
<head>
<meta charset="utf-8">
<title>Slate Haven – Questions</title>
<link href="https://fonts.googleapis.com/css2?family=Arimo:wght@400;700&family=Marcellus&display=swap" rel="stylesheet">
<style>
:root{
  --teal:#4f8f89;
  --teal-dark:#3f7873;
  --teal-video:#5a968f;
  --gold:#f4b400;
  --white:#ffffff;
  --ink:#222222;
  --muted:#a9a9a9;
  --panel:#f3f3f3;
  --panel-line:#dcdcdc;
  --band-top:#e2e2e2;
  --body-text:#333333;
}
*{margin:0;padding:0;box-sizing:border-box}
html,body{width:1200px;height:1010px;overflow:hidden;background:var(--white);font-family:"Arimo",Arial,sans-serif}
.page{position:relative;width:1200px;height:1010px;overflow:hidden}
.header{position:absolute;left:0;top:0;width:1200px;height:94px;background:var(--teal);border-top:4px solid var(--teal-dark)}
.brand{position:absolute;left:262px;top:26px;display:flex;align-items:center;gap:10px;color:var(--white);font-weight:700;font-size:24px;letter-spacing:1px}
.brand-square{width:26px;height:26px;background:var(--gold)}
.cart-widget{position:absolute;left:852px;top:0;width:104px;height:30px;background:var(--teal-dark);border-radius:0 0 6px 6px;display:flex;align-items:center;gap:6px;padding-left:8px;color:var(--white);font-size:8px;line-height:10px}
.cart-widget .dot{width:14px;height:14px;border-radius:50%;background:var(--gold);flex:none}
.cart-widget b{color:var(--gold);font-weight:700}
.nav{position:absolute;top:58px;left:0;height:29px;width:1200px}
.nav a{position:absolute;top:0;height:29px;line-height:29px;color:var(--white);font-size:11.5px;font-weight:700;text-decoration:none}
.nav a.active{background:var(--gold);border-radius:4px;padding:0 14px;color:var(--white)}
.title-band{position:absolute;left:0;top:94px;width:1200px;height:112px;background:linear-gradient(var(--band-top),var(--white))}
.page-title{position:absolute;left:294px;top:126px;font-family:"Marcellus",Georgia,serif;font-size:28px;color:var(--ink)}
.title-icon{position:absolute;left:250px;top:130px}
.quote-panel{position:absolute;left:245px;top:216px;width:245px;height:634px;background:var(--panel);border:2px solid var(--panel-line);border-radius:10px}
.quote-lead{position:absolute;left:265px;top:244px;width:210px;font-size:19px;line-height:26px;color:var(--muted)}
.kitchen-photo{position:absolute;left:254px;top:336px;width:226px;height:130px;background:linear-gradient(90deg,#9bb9c9,#8d2a2a 40%,#2c2c34 70%,#2b3a8c)}
.form-row{position:absolute;left:263px;font-size:15px;font-weight:700;color:var(--muted)}
.form-row.fax{font-weight:700}
.form-row .val{position:absolute;left:66px;top:0;font-weight:400;white-space:nowrap}
.field{position:absolute;left:334px;width:129px;height:21px;background:var(--white);border:1px solid #c8c8c8}
.field.select::after{content:"";position:absolute;right:0;top:0;width:20px;height:19px;background:#ececec;border-left:1px solid #c8c8c8}
.select-arrow{position:absolute;right:6px;top:7px;z-index:1}
.section-title{position:absolute;left:582px;top:210px;font-family:"Marcellus",Georgia,serif;font-size:28px;color:var(--ink)}
.video-icon{position:absolute;left:534px;top:216px}
.video{position:absolute;left:531px;top:261px;width:422px;height:270px;border-radius:8px 8px 0 0;overflow:hidden;background:var(--teal-video);box-shadow:0 10px 8px -6px rgba(0,0,0,.25)}
.video-screen{position:absolute;left:0;top:0;width:422px;height:246px;background:linear-gradient(var(--teal-video),#4f8a84)}
.play{position:absolute;left:188px;top:117px;width:46px;height:32px;background:#1d1d1d;border-radius:6px}
.controls{position:absolute;left:0;top:246px;width:422px;height:24px;background:linear-gradient(#f4f4f4,#d6d6d6)}
.faq-title{position:absolute;left:531px;top:584px;font-family:"Marcellus",Georgia,serif;font-size:30px;color:var(--ink)}
.faq{position:absolute;left:531px;top:630px;width:430px;font-size:9.5px;line-height:13.7px;color:var(--body-text)}
.faq p{margin-bottom:13.7px}
.faq .q{font-weight:700;margin-bottom:0}
.footer-gap{position:absolute;left:0;top:880px;width:1200px;height:29px;background:linear-gradient(var(--white),#dedede)}
.footer{position:absolute;left:0;top:909px;width:1200px;height:101px;background:var(--teal)}
.footer ul{position:absolute;top:24px;list-style:none}
.footer li{height:22px;font-size:9.5px;font-weight:700;color:var(--white);padding-left:10px;position:relative}
.footer li::before{content:"";position:absolute;left:0;top:4px;width:4px;height:4px;border-top:1px solid var(--white);border-right:1px solid var(--white);transform:rotate(45deg)}
.footer-brand{position:absolute;left:870px;top:30px;display:flex;align-items:center;gap:6px;color:var(--white);font-weight:700;font-size:14px}
.footer-brand .brand-square{width:12px;height:12px}
.copyright{position:absolute;left:868px;top:59px;font-size:9.5px;line-height:13px;color:var(--white)}
</style>
</head>
<body>
<div class="page">
  <header class="header">
    <div class="brand"><span class="brand-square"></span>Slate Haven</div>
    <div class="cart-widget"><span class="dot"></span><span>Now in your cart<br><b>0 items</b></span></div>
    <nav class="nav">
      <a class="active" href="#" style="left:497px">HOME</a>
      <a href="#" style="left:584px">GALLERY</a>
      <a href="#" style="left:675px">QUESTIONS</a>
      <a href="#" style="left:777px">ORDERR</a>
      <a href="#" style="left:864px">SHOPPING CART</a>
    </nav>
  </header>

  <div class="title-band"></div>
  <svg class="title-icon" width="34" height="38" viewBox="0 0 34 38" aria-hidden="true">
    <rect x="4" y="4" width="26" height="30" rx="3" fill="#2f6fc4" transform="rotate(-8 17 19)"/>
    <text x="17" y="28" text-anchor="middle" font-family="Arimo, sans-serif" font-size="22" font-weight="700" fill="#fff">?</text>
  </svg>
  <h1 class="page-title">Questions</h1>

  <section class="quote-panel"></section>
  <p class="quote-lead">Will Calculat how much stone mai need sent us a Progrem!</p>
  <div class="kitchen-photo" role="img" aria-label="Kitchen with red cabinets and granite counters"></div>

  <div class="form-row fax" style="top:484px">FAX<span class="val">:&nbsp;&nbsp;800-555-0142</span></div>
  <div class="form-row" style="top:516px">Upload :</div>
  <div class="field select" style="top:516px"><svg class="select-arrow" width="8" height="5" viewBox="0 0 8 5"><path d="M0 0h8L4 5z" fill="#555"/></svg></div>
  <div class="form-row" style="top:551px">Name&nbsp;&nbsp;:</div>
  <div class="field" style="top:551px"></div>
  <div class="form-row" style="top:588px">Phone&nbsp;:</div>
  <div class="field" style="top:588px"></div>
  <div class="form-row" style="top:624px">Email&nbsp;&nbsp;:</div>
  <div class="field" style="top:624px"></div>

  <svg class="video-icon" width="26" height="28" viewBox="0 0 26 28" aria-hidden="true">
    <rect x="1" y="6" width="22" height="20" fill="#333"/>
    <rect x="4" y="1" width="20" height="6" fill="#555" transform="rotate(-10 14 4)"/>
  </svg>
  <h2 class="section-title">Installation video</h2>
  <div class="video">
    <div class="video-screen" role="img" aria-label="Installation video preview"></div>
    <div class="play"><svg width="46" height="32" viewBox="0 0 46 32"><path d="M18 9l12 7-12 7z" fill="#fff"/></svg></div>
    <svg class="controls" width="422" height="24" viewBox="0 0 422 24">
      <path d="M6 7l7 5-7 5z" fill="#333"/>
      <path d="M22 10h3l4-3v10l-4-3h-3z" fill="#333"/>
      <text x="45" y="15" font-family="Arimo, sans-serif" font-size="8" fill="#333">0:00 / 3:05</text>
      <rect x="92" y="10" width="282" height="4" rx="2" fill="#9a9a9a"/>
      <circle cx="96" cy="12" r="4" fill="#666"/>
      <rect x="384" y="8" width="12" height="8" rx="1" fill="#333"/>
      <path d="M404 7h4M404 7v4M416 7h-4M416 7v4M404 17h4M404 17v-4M416 17h-4M416 17v-4" stroke="#333" stroke-width="1.5" fill="none"/>
    </svg>
  </div>

  <h2 class="faq-title">FAQ</h2>
  <div class="faq">
    <p>We often receive emails/irc messages about colors and color problems. Here are some Frequently Asked Questions with their answers.</p>
    <p class="q">Q: Does Chatly support colored messages?</p>
    <p>A: Yes, with the color popup menu in the input line users can add a color to their text.</p>
    <p class="q">Q: Since when is this possible?</p>
    <p>A: Chatly has had the color capability since version 2.5, released in May 1996. Chatly 2.5 did not have a color popup menu so color codes had to be entered manually. With the popup menu in Chatly 3.0 one has an easy way to write colored text.</p>
    <p class="q">Q: So how does it actually work?</p>
    <p>A: After you press return Chatly checks if the text you entered has colors. It will then encode that line into something that can be transferred through IRC servers. Specifically it will insert control-C characters plus one other character for every color you used. Basically users do not have to remember codes or something to write colored messages.</p>
  </div>

  <div class="footer-gap"></div>
  <footer class="footer">
    <ul style="left:243px"><li>Home</li><li>Gallery</li><li>Questions</li></ul>
    <ul style="left:350px"><li>Orderr</li><li>Shopping Cart</li><li>Contact Us</li></ul>
    <ul style="left:477px"><li>Return Policy</li><li>Shipping Policy</li><li>Privacy</li></ul>
    <ul style="left:596px"><li>Terms of Use</li><li>Customer Service</li></ul>
    <div class="footer-brand"><span class="brand-square"></span>Slate Haven</div>
    <p class="copyright">© 2011 slatehaven.com.<br>All Rights Reserved.</p>
  </footer>
</div>
</body>
</html>
```